New web page, 2 companies on the one page

A new web page for an engineering consultancy and maintenance management company

Corlett & Associates is the parent company covering the design and consultancy
Valtrix Engineering is the Maintenance and Reliability company

Target Market(s)

Food & Beverage, ingredients Manufacturing
engineering managers

Coding

Coded - Design and coding required

Number of Pages Required

1 page

Font styles to use
Other font styles liked:
• Roboto

Colors
1861ab
85acd3
d0dfed
cee9f5

```html
<!DOCTYPE html>
<html lang="en">
<head>
<meta charset="utf-8">
<title>Corlett &amp; Associates — Engineering Consultancy &amp; Maintenance Management</title>
<link rel="stylesheet" href="https://fonts.googleapis.com/css2?family=Roboto:ital,wght@0,400;0,500;0,700;0,900;1,400&family=Lato:wght@400;700&display=swap">
<style>
:root{
  --blue:#17a0dc;
  --navy:#1861ab;
  --sky:#85acd3;
  --mist:#d0dfed;
  --ice:#cee9f5;
  --dark:#1c1d22;
  --ink:#1f2127;
  --grey:#666a70;
  --soft:#f3f3f3;
  --white:#ffffff;
}
*{margin:0;padding:0;box-sizing:border-box}
html,body{width:1200px;height:3949px;overflow:hidden;background:var(--white)}
body{position:relative;font-family:"Roboto",Arial,sans-serif;color:var(--ink)}

/* header */
.site-header{position:absolute;left:0;top:0;width:1200px;height:92px;background:var(--white);border-top:3px solid var(--blue);z-index:3}
.nav-pointer{position:absolute;left:515px;top:0;width:0;height:0;border-left:9px solid transparent;border-right:9px solid transparent;border-top:10px solid var(--blue)}
.brand{position:absolute;left:141px;top:28px;display:flex;align-items:center;gap:12px}
.brand-mark{width:30px;height:30px;background:var(--dark);border-radius:4px}
.brand-name{font-weight:700;font-size:23px;color:var(--dark);letter-spacing:.3px}
.main-nav a{position:absolute;top:37px;font-size:14px;font-weight:700;color:var(--ink);text-decoration:none;letter-spacing:.2px}
.main-nav a.is-active{color:var(--blue)}

/* hero */
.hero{position:absolute;left:0;top:92px;width:1200px;height:680px}
.hero-photo{position:absolute;inset:0;background:linear-gradient(180deg,#0b6fbd 0%,#1b8fdc 40%,#3f6f92 70%,#233648 100%)}
.hero-panel{position:absolute;left:110px;top:178px;width:719px;height:233px;background:rgba(28,38,56,.62)}
.hero-title{position:absolute;left:142px;top:196px;font-size:40px;line-height:41px;font-weight:700;color:var(--white);text-transform:uppercase;letter-spacing:.2px}
.btn-start{position:absolute;left:144px;top:337px;width:136px;height:42px;background:var(--blue);color:var(--white);font-size:14px;font-weight:700;display:flex;align-items:center;justify-content:center}
.hero-dots{position:absolute;left:142px;top:496px;display:flex;gap:5px}
.hero-dots span{width:10px;height:10px;border-radius:50%;background:var(--white)}
.hero-dots span:first-child{background:var(--blue)}
.hero-edge{position:absolute;left:0;top:640px;width:1200px;height:136px}

/* section titles */
.section-title{position:absolute;left:0;width:1200px;text-align:center;font-size:33px;font-weight:700;color:var(--ink);text-transform:uppercase}
.section-title em{font-style:normal;color:var(--blue)}
.title-rule{position:absolute;left:570px;width:60px;height:3px;background:var(--blue)}

/* services */
.services-diagram{position:absolute;left:0;top:900px;width:1200px;height:600px}
.svc-label{position:absolute;font-size:14px;line-height:21px;color:var(--grey)}
.svc-label.right{text-align:right}

/* about */
.about-band{position:absolute;left:0;top:1571px;width:1200px;height:728px}
.about-photo{position:absolute;left:141px;top:1745px;width:385px;height:375px;border-radius:6px;background:linear-gradient(160deg,#d9e6ee 0%,#9ec6df 45%,#3b8cc3 100%)}
.about-title{position:absolute;left:584px;top:1805px;font-size:31px;font-weight:700;color:var(--white);text-transform:uppercase}
.about-rule{position:absolute;left:584px;top:1866px;width:86px;height:2px;background:var(--white)}
.about-copy{position:absolute;left:584px;top:1884px;width:474px;font-family:"Lato",Arial,sans-serif;font-size:12.5px;line-height:21px;color:var(--white);text-align:justify}
.about-copy p{margin-bottom:21px}

/* blog */
.blog-card{position:absolute;top:2476px;width:291px;text-align:center}
.blog-image{width:291px;height:237px;clip-path:polygon(0 0,100% 0,100% 84%,50% 100%,0 84%)}
.blog-title{margin-top:29px;font-size:20px;line-height:25px;font-weight:700;color:var(--ink)}
.blog-date{margin-top:5px;font-size:13px;font-weight:700;color:var(--blue)}
.blog-text{margin-top:8px;font-size:12.5px;line-height:20.5px;color:var(--grey);padding:0 8px}

/* testimonials */
.testimonials{position:absolute;left:0;top:2963px;width:1200px;height:580px;background:var(--soft)}
.testimonials-rule{position:absolute;left:0;top:2961px;width:1200px;height:5px;background:linear-gradient(90deg,var(--dark) 0%,var(--dark) 55%,var(--blue) 100%)}
.client-photo{position:absolute;left:273px;top:3150px;width:178px;height:178px;border-radius:50%;border:3px solid var(--blue);background:radial-gradient(circle at 50% 40%,#d8b9a0 0%,#8e7a6c 45%,#2e5377 100%)}
.quote{position:absolute;left:478px;top:3166px;width:434px;font-size:12.5px;line-height:20.7px;font-style:italic;color:var(--grey);text-align:justify}
.client-name{position:absolute;left:478px;top:3287px;font-size:18px;font-weight:500;color:var(--ink)}
.client-name small{font-size:12px;font-weight:400;color:var(--grey);margin-left:6px}
.slider-arrow{position:absolute;top:3219px;width:24px;height:24px}

/* footer */
.footer-edge{position:absolute;left:0;top:3400px;width:1200px;height:130px}
.site-footer{position:absolute;left:0;top:3528px;width:1200px;height:421px;background:#0b0b0d;color:var(--white)}
.footer-brand{position:absolute;left:500px;top:3519px;display:flex;align-items:center;gap:12px}
.footer-brand .dot{width:26px;height:26px;border-radius:50%;background:var(--blue)}
.footer-brand span{font-size:22px;font-weight:700;color:var(--white)}
.footer-heading{position:absolute;top:3615px;font-size:15px;font-weight:700;color:var(--white)}
.footer-links{position:absolute;left:138px;top:3657px;list-style:none}
.footer-links li{font-size:12px;line-height:30.4px;color:var(--white)}
.footer-links li::before{content:"»";margin-right:12px}
.contact-item{position:absolute;left:293px;display:flex;align-items:center;gap:18px;font-size:12px;line-height:19px;color:var(--white)}
.contact-icon{width:34px;height:34px;border:1.5px solid var(--white);border-radius:50%;display:flex;align-items:center;justify-content:center;flex:none}
.field{position:absolute;background:var(--white);font-size:10px;color:#888;padding:6px 10px}
.btn-submit{position:absolute;left:981px;top:3824px;width:77px;height:28px;background:var(--blue);border-radius:4px;color:var(--white);font-size:12px;font-weight:700;display:flex;align-items:center;justify-content:center}
.footer-rule{position:absolute;left:135px;top:3872px;width:923px;height:1px;background:#2d2e33}
.copyright{position:absolute;left:135px;top:3895px;font-size:11.5px;color:var(--white)}
.social{position:absolute;top:3888px;width:28px;height:28px;border-radius:50%;border:1.5px solid var(--white)}
.social.is-blue{background:var(--blue);border-color:var(--blue)}
</style>
</head>
<body>

<header class="site-header">
  <span class="nav-pointer"></span>
  <div class="brand"><span class="brand-mark"></span><span class="brand-name">Corlett &amp; Associates</span></div>
  <nav class="main-nav">
    <a class="is-active" style="left:503px">HOME</a>
    <a style="left:578px">ABOUT US</a>
    <a style="left:685px">SERVICES</a>
    <a style="left:789px">BLOG</a>
    <a style="left:863px">REVIEWS</a>
    <a style="left:961px">CONTACT US</a>
  </nav>
</header>

<section class="hero">
  <div class="hero-photo" role="img" aria-label="Industrial processing plant with towers and pipework under a blue sky"></div>
  <div class="hero-panel"></div>
  <h1 class="hero-title">We are an engineering<br>consultancy &amp; maintenance<br>management</h1>
  <a class="btn-start">GET STARTED</a>
  <div class="hero-dots"><span></span><span></span><span></span><span></span></div>
</section>
<svg class="hero-edge" viewBox="0 640 1200 136" preserveAspectRatio="none" aria-hidden="true">
  <polygon points="0,668 584,768 615,768 1200,668 1200,776 0,776" fill="#ffffff"/>
  <polygon points="0,652 584,752 584,766 0,668" fill="#17a0dc"/>
  <polygon points="615,752 1200,652 1200,668 615,766" fill="#17a0dc"/>
</svg>

<h2 class="section-title" style="top:850px">Our <em>Services</em></h2>
<span class="title-rule" style="top:907px"></span>

<svg class="services-diagram" viewBox="0 900 1200 600" aria-label="Services around a central hub">
  <defs>
    <radialGradient id="hub" cx="50%" cy="45%" r="55%">
      <stop offset="0" stop-color="#d9eef8"/>
      <stop offset="1" stop-color="#a9d6ec"/>
    </radialGradient>
  </defs>
  <circle cx="599" cy="1211" r="219" fill="url(#hub)" role="img" aria-label="Engineers at work, tinted light blue"/>
  <g stroke="#ffffff" stroke-width="5">
    <circle cx="599" cy="998" r="40" fill="#17a0dc"/>
    <circle cx="376" cy="1193" r="40" fill="#17a0dc"/>
    <circle cx="819" cy="1193" r="40" fill="#17a0dc"/>
    <circle cx="524" cy="1436" r="40" fill="#17a0dc"/>
    <circle cx="670" cy="1436" r="40" fill="#17a0dc"/>
    <circle cx="455" cy="1058" r="40" fill="#1c1d22"/>
    <circle cx="739" cy="1058" r="40" fill="#1c1d22"/>
    <circle cx="411" cy="1346" r="40" fill="#1c1d22"/>
    <circle cx="783" cy="1346" r="40" fill="#1c1d22"/>
  </g>
  <g fill="none" stroke="#ffffff" stroke-width="2" stroke-linecap="round">
    <g transform="translate(599 998)"><rect x="-15" y="-11" width="30" height="20" rx="2"/><line x1="0" y1="9" x2="0" y2="14"/><line x1="-8" y1="14" x2="8" y2="14"/><circle cx="9" cy="-11" r="5"/></g>
    <g transform="translate(455 1058)"><circle r="7"/><circle r="13" stroke-width="4" stroke-dasharray="4 3"/></g>
    <g transform="translate(739 1058)"><rect x="-14" y="-4" width="10" height="18"/><rect x="-2" y="-14" width="7" height="28"/><rect x="7" y="2" width="8" height="12"/><circle cx="11" cy="-10" r="4"/></g>
    <g transform="translate(376 1193)"><line x1="-13" y1="-13" x2="13" y2="13"/><line x1="13" y1="-13" x2="-13" y2="13"/><circle cx="-13" cy="-13" r="4"/><circle cx="13" cy="-13" r="4"/></g>
    <g transform="translate(819 1193)"><path d="M-15 4 A15 15 0 0 1 15 4 Z"/><line x1="-18" y1="6" x2="18" y2="6"/><rect x="-11" y="10" width="22" height="6" rx="3"/></g>
    <g transform="translate(411 1346)"><rect x="-15" y="-11" width="30" height="20" rx="2"/><circle cx="0" cy="-1" r="5"/><line x1="-8" y1="14" x2="8" y2="14"/></g>
    <g transform="translate(783 1346)"><circle r="14"/><circle r="8"/><circle r="2.5"/></g>
    <g transform="translate(524 1436)"><circle cx="-7" cy="-8" r="5"/><circle cx="8" cy="-8" r="5"/><path d="M-16 12 a9 9 0 0 1 18 0 M-1 12 a9 9 0 0 1 18 0"/></g>
    <g transform="translate(670 1436)"><path d="M-16 -2 L-6 -10 L4 -4 L16 -10 M-16 -2 L-4 10 L8 2 L16 -2"/><line x1="-6" y1="2" x2="2" y2="8"/></g>
  </g>
</svg>

<div class="svc-label" style="left:499px;top:932px;width:200px;text-align:center">Maintenance Execution</div>
<div class="svc-label right" style="left:157px;top:1030px;width:240px">Engineering &amp; Maintenance<br>Management</div>
<div class="svc-label" style="left:796px;top:1029px">Manufacturing Performance<br>Measurement</div>
<div class="svc-label right" style="left:67px;top:1168px;width:250px">Major Equipment and Services<br>Installation &amp; Commissioning.</div>
<div class="svc-label" style="left:875px;top:1182px">SCADA</div>
<div class="svc-label right" style="left:193px;top:1318px;width:160px">Project<br>Management</div>
<div class="svc-label" style="left:840px;top:1318px">Vision Inspection<br>Systems</div>
<div class="svc-label right" style="left:264px;top:1409px;width:200px">Process &amp; Facilities<br>Design</div>
<div class="svc-label" style="left:728px;top:1423px">Acquisition Due<br>Diligence</div>

<svg class="about-band" viewBox="0 0 1200 728" preserveAspectRatio="none" aria-hidden="true">
  <defs>
    <linearGradient id="aboutBg" x1="0" y1="0" x2="1" y2="1">
      <stop offset="0" stop-color="#0d85c6"/>
      <stop offset=".5" stop-color="#1a9fe0"/>
      <stop offset="1" stop-color="#0e7fbf"/>
    </linearGradient>
  </defs>
  <polygon points="0,92 584,0 584,22 0,112" fill="#1c1d22"/>
  <polygon points="615,0 1200,92 1200,112 615,22" fill="#1c1d22"/>
  <polygon points="0,114 584,24 615,24 1200,114 1200,604 615,704 584,704 0,604" fill="url(#aboutBg)" role="img" aria-label="Factory pipework tinted blue"/>
  <polygon points="0,606 584,706 584,728 0,626" fill="#1c1d22"/>
  <polygon points="615,706 1200,606 1200,626 615,728" fill="#1c1d22"/>
</svg>
<div class="about-photo" role="img" aria-label="Two engineers in white coats reviewing a tablet on the factory floor"></div>
<h2 class="about-title">About Corlett Associates</h2>
<span class="about-rule"></span>
<div class="about-copy">
  <p>Corlett &amp; Associates is specialised manufacturing engineering support organisation that can provide fast, nimble, and flexible services.</p>
  <p>We have a proven track record in delivering tangible outcomes in process design and fit-out, project management, manufacturing process and maintenance design and execution.</p>
  <p>Our specialist focus in food manufacturing across a range of sectors allows our team to deliver real benefits to performance and recognition of the clients investment</p>
</div>

<h2 class="section-title" style="top:2387px">Our <em>Latest Blog</em></h2>
<span class="title-rule" style="top:2444px"></span>

<article class="blog-card" style="left:144px">
  <div class="blog-image" role="img" aria-label="Food technologists in hairnets checking a tablet in a production hall" style="background:linear-gradient(160deg,#eef2f5 0%,#c9d6df 60%,#8ea3b3 100%)"></div>
  <h3 class="blog-title">Lorem ipsum dolor sit<br>amet,consectetur</h3>
  <div class="blog-date">&#9638; Jan 20,2021</div>
  <p class="blog-text">Lorem ipsum dolor sit amet, consectetur adipis cing elit, sed do eiusmod tempor incididunt ut labore et dolore magna aliqua.</p>
</article>
<article class="blog-card" style="left:455px">
  <div class="blog-image" role="img" aria-label="Forklift carrying sacks of ingredients in a warehouse" style="background:linear-gradient(160deg,#c8703a 0%,#8a5a3c 45%,#d6c07a 75%,#5a5048 100%)"></div>
  <h3 class="blog-title">Lorem ipsum dolor sit<br>amet,consectetur</h3>
  <div class="blog-date">&#9638; Jan 20,2021</div>
  <p class="blog-text">Lorem ipsum dolor sit amet, consectetur adipis cing elit, sed do eiusmod tempor incididunt ut labore et dolore magna aliqua.</p>
</article>
<article class="blog-card" style="left:765px">
  <div class="blog-image" role="img" aria-label="Two quality inspectors in white coats reviewing notes on a production line" style="background:linear-gradient(160deg,#f1f1ef 0%,#cfcfca 55%,#8f948f 100%)"></div>
  <h3 class="blog-title">Lorem ipsum dolor sit<br>amet,consectetur</h3>
  <div class="blog-date">&#9638; Jan 20,2021</div>
  <p class="blog-text">Lorem ipsum dolor sit amet, consectetur adipis cing elit, sed do eiusmod tempor incididunt ut labore et dolore magna aliqua.</p>
</article>

<section class="testimonials"></section>
<span class="testimonials-rule"></span>
<h2 class="section-title" style="top:3056px">Our <em>Testimonials</em></h2>
<span class="title-rule" style="top:3111px"></span>
<div class="client-photo" role="img" aria-label="Portrait of a smiling client"></div>
<p class="quote">“Lorem ipsum dolor sit amet, consectetur adipiscing elit, sed do eiusmod tempor incididunt ut labore et dolore magna aliqua. Ut enim ad minim veniam, quis nostrud exercitation ullamco laboris nisi ut aliquip ex ea commodo consequat. Duis aute irure dolor in reprehenderit in voluptate velit esse cillum dolore eu”</p>
<div class="client-name">Marco Bellini<small>Company name</small></div>
<svg class="slider-arrow" style="left:135px" viewBox="0 0 24 24" aria-label="Previous"><polyline points="15,5 8,12 15,19" fill="none" stroke="#555" stroke-width="2"/></svg>
<svg class="slider-arrow" style="left:1036px" viewBox="0 0 24 24" aria-label="Next"><polyline points="9,5 16,12 9,19" fill="none" stroke="#555" stroke-width="2"/></svg>

<svg class="footer-edge" viewBox="0 3400 1200 130" preserveAspectRatio="none" aria-hidden="true">
  <polygon points="0,3530 584,3424 615,3424 1200,3530" fill="#0b0b0d"/>
  <polygon points="0,3514 584,3410 584,3424 0,3530" fill="#17a0dc"/>
  <polygon points="615,3410 1200,3514 1200,3530 615,3424" fill="#17a0dc"/>
  <polygon points="584,3416 615,3416 615,3424 584,3424" fill="#0b0b0d"/>
</svg>

<footer class="site-footer"></footer>
<div class="footer-brand"><span class="dot"></span><span>Valtrix Engineering</span></div>

<h4 class="footer-heading" style="left:135px">Useful Links</h4>
<ul class="footer-links">
  <li>Home</li><li>About</li><li>Blog</li><li>Services</li><li>Reviews</li><li>Contact</li>
</ul>

<h4 class="footer-heading" style="left:293px">Contact Information</h4>
<div class="contact-item" style="top:3657px">
  <span class="contact-icon"><svg width="14" height="14" viewBox="0 0 24 24"><path d="M12 2a7 7 0 0 0-7 7c0 5 7 13 7 13s7-8 7-13a7 7 0 0 0-7-7z" fill="none" stroke="#fff" stroke-width="2.2"/><circle cx="12" cy="9" r="2.5" fill="#fff"/></svg></span>
  <span>Lorem ipsum dolor sit amet,<br>consectetur adipiscing elit, sed do</span>
</div>
<div class="contact-item" style="top:3706px">
  <span class="contact-icon"><svg width="14" height="14" viewBox="0 0 24 24"><path d="M6 3l3 5-2 2a12 12 0 0 0 7 7l2-2 5 3-2 4C10 22 2 14 2 5z" fill="#fff"/></svg></span>
  <span>Phone : +1 555 014 2290</span>
</div>
<div class="contact-item" style="top:3752px">
  <span class="contact-icon"><svg width="14" height="14" viewBox="0 0 24 24"><rect x="3" y="6" width="18" height="13" rx="1.5" fill="#fff"/><polyline points="3,7 12,14 21,7" fill="none" stroke="#0b0b0d" stroke-width="1.8"/></svg></span>
  <span>Email : info@corlettassoc.com</span>
</div>
<div class="contact-item" style="top:3800px">
  <span class="contact-icon"><svg width="14" height="14" viewBox="0 0 24 24"><rect x="4" y="9" width="16" height="11" rx="1.5" fill="#fff"/><rect x="7" y="3" width="10" height="7" fill="none" stroke="#fff" stroke-width="2"/></svg></span>
  <span>Fax: 0661-48217</span>
</div>

<h4 class="footer-heading" style="left:596px">Get In Touch:</h4>
<div class="field" style="left:599px;top:3657px;width:224px;height:29px">Name :</div>
<div class="field" style="left:832px;top:3657px;width:224px;height:29px">Phone :</div>
<div class="field" style="left:599px;top:3698px;width:457px;height:30px">Email :</div>
<div class="field" style="left:599px;top:3738px;width:457px;height:65px">Message :</div>
<a class="btn-submit">SUBMIT</a>

<span class="footer-rule"></span>
<p class="copyright">Copyrights © 2021, Company name. All Rights Reserved. &nbsp;|&nbsp; Privacy policy</p>
<span class="social" style="left:950px" aria-label="Social profile"></span>
<span class="social is-blue" style="left:985px" aria-label="Social profile"></span>
<span class="social" style="left:1019px" aria-label="Social profile"></span>

</body>
</html>
```